Larkhollow needs a Webpage Design

We need a webpage for Dr. XYZ who is doing consultancy practice in the area of speech, language, and reading disabilities. He is doing his consultancy practice as "Larkhollow Consultants". Our target market is clients with annual income of $100,000 or more in Chicago area. Our business philosophy is: "...We provide the best evidence-based services/interventions, at an affordable fee, and deal only with clients who seek such services...."

Dr. XYZ's area of research interests are: a) using assistive technology for communication for children with autism, b) early intervention with focus on parent participation, and c) language learning for children birth-to-five years.

He works at a public university whose school color is 'Orange". Home page should show two logos (university and practice). Each page should stand on its own and reflect the content with minimal scrolling. The colors should be subdued (not bright colors) to attract college educated wealthy individuals who are seeking best evidence-based practice in speech, language, and reading for their children.

We need five pages: Home, Consultation, Research, Professional Development, and Contact (with google map directions). The home page should have space for a picture and links for facebook, twitter, and google plus. Other pages should have space for at least one picture and links to pdf files.

The overall design should show healthcare service, evidence-based early intervention with focus on parent participation, and project that we are leaders in the field.

```html
<!DOCTYPE html>
<html lang="en">
<head>
<meta charset="utf-8">
<title>Larkhollow Consultants</title>
<link href="https://fonts.googleapis.com/css2?family=Varela+Round&family=Open+Sans:wght@400;600;700&display=swap" rel="stylesheet">
<style>
  :root{
    --brand:#2878bf;
    --brand-dark:#1d63a6;
    --nav:#2e2e2e;
    --ink:#333;
    --muted:#777;
    --band:#f1f1f1;
    --line:#dcdcdc;
    --white:#fff;
    --hero-a:#c9a27e;
    --hero-b:#6d89a8;
  }
  *{box-sizing:border-box;margin:0;padding:0}
  html,body{width:814px;height:1200px;overflow:hidden;background:var(--white)}
  body{font-family:"Open Sans",Arial,sans-serif;color:var(--ink);position:relative}
  .wrap{width:654px;margin:0 auto;position:relative}

  /* header */
  .site-header{height:125px;position:relative}
  .brand{position:absolute;left:0;top:14px;font-family:"Varela Round",sans-serif;color:var(--brand);line-height:1}
  .brand-name{font-size:34px;display:block}
  .brand-sub{font-size:22px;display:block;margin-left:56px;margin-top:2px}
  .practitioner{position:absolute;left:286px;top:40px;font-family:"Varela Round",sans-serif;font-size:22px;color:var(--brand);font-weight:700}
  .contact-line{position:absolute;left:0;top:92px;font-size:12px;color:var(--brand);font-weight:600}
  .contact-line span{color:var(--ink)}

  /* nav */
  .main-nav{height:28px;background:var(--nav);display:flex;align-items:center;padding-left:14px}
  .main-nav a{color:var(--white);text-decoration:none;font-size:10.5px;letter-spacing:.4px;margin-right:42px}

  /* hero */
  .hero{height:290px;position:relative;background:linear-gradient(120deg,var(--hero-b) 0%,#9aa9b6 45%,var(--hero-a) 100%)}
  .hero-caption{position:absolute;left:16px;top:96px;color:var(--white);font-size:22px;line-height:1.28;font-weight:600;text-shadow:0 1px 3px rgba(0,0,0,.35);width:420px}
  .hero-dots{position:absolute;bottom:12px;left:50%;transform:translateX(-50%);display:flex;gap:7px}
  .hero-dots i{width:8px;height:8px;border-radius:50%;background:rgba(255,255,255,.6);display:block}
  .hero-dots i.on{background:var(--white)}

  /* welcome */
  .welcome{text-align:center;padding:24px 0 22px}
  h2.section-title{font-family:"Varela Round",sans-serif;font-weight:400;font-size:21px;line-height:1.2;color:var(--ink);margin-bottom:12px}
  .welcome p{font-size:9.5px;line-height:1.55;color:var(--muted);padding:0 10px}
  .read-more{display:inline-block;margin-top:12px;font-size:9px;color:var(--brand);text-decoration:none;padding:0 18px 4px;border-bottom:2px solid var(--brand);letter-spacing:.4px}

  /* services */
  .services{background:var(--band);padding:20px 0 22px;text-align:center}
  .service-grid{display:flex;justify-content:space-between;margin-top:10px}
  .service-card{width:204px;background:var(--white);border:1px solid var(--line);padding:10px 10px 10px}
  .service-media{height:96px;display:block}
  .m1{background:linear-gradient(135deg,#5f7f93,#c7b79d)}
  .m2{background:linear-gradient(135deg,#d9c2aa,#8aa7c2)}
  .m3{background:linear-gradient(135deg,#b9a89b,#7e8f9f)}
  .service-card h3{font-family:"Varela Round",sans-serif;font-weight:400;font-size:11px;color:var(--brand);margin:10px 0 5px;white-space:nowrap}
  .service-card p{font-size:8.5px;line-height:1.5;color:var(--muted)}
  .learn-more{display:inline-block;margin-top:5px;font-size:9px;color:var(--brand);text-decoration:none}

  /* lower */
  .lower{display:flex;justify-content:space-between;padding-top:16px}
  .research{width:390px}
  .research h2,.pro-dev h2{font-family:"Varela Round",sans-serif;font-weight:400;font-size:17px;line-height:1.2;color:var(--ink);margin-bottom:10px;white-space:nowrap}
  .research-body{display:flex;gap:14px}
  .research-media{width:150px;height:86px;flex:none;background:linear-gradient(135deg,#e7dcc4,#b9ab8d)}
  .updates{list-style:none;flex:1}
  .updates li{font-size:8.5px;line-height:1.4;color:var(--muted);padding-left:14px;position:relative;margin-bottom:5px}
  .updates li svg{position:absolute;left:0;top:2px}
  .research .read-more{margin-top:2px;margin-left:164px;padding:0 10px 3px}
  .pro-dev{width:240px}
  .pd-item{display:flex;gap:8px;margin-bottom:8px}
  .pd-media{width:54px;height:40px;flex:none;background:linear-gradient(135deg,#8ea1b3,#cdb9a4)}
  .pd-item p{font-size:8.5px;line-height:1.4;color:var(--muted)}
  .pd-item small{display:block;font-size:7.5px;color:var(--brand);margin-top:1px}

  /* footer */
  .site-footer{position:absolute;left:0;right:0;bottom:0;height:72px;background:var(--brand-dark);color:var(--white)}
  .site-footer .wrap{height:72px}
  .footer-links{position:absolute;left:0;top:20px;font-size:9px}
  .footer-links a{color:var(--white);text-decoration:none}
  .copyright{position:absolute;left:0;top:42px;font-size:8px;opacity:.85}
  .connect{position:absolute;right:0;top:12px;text-align:center}
  .connect span{font-size:11px;display:block;margin-bottom:5px}
  .social{display:flex;gap:6px;justify-content:center}
  .social i{width:20px;height:20px;border-radius:50%;background:var(--white);display:block}
</style>
</head>
<body>
  <header class="site-header wrap">
    <div class="brand"><span class="brand-name">Larkhollow</span><span class="brand-sub">Consultants</span></div>
    <div class="practitioner">Dr XYZ</div>
    <div class="contact-line">Email : <span>info@larkhollow.com</span></div>
  </header>

  <nav class="main-nav wrap">
    <a href="#">HOME</a><a href="#">CONSULTATION</a><a href="#">RESEARCH</a><a href="#">PROFESSIONAL DEVELOPMENT</a><a href="#">CONTACT</a>
  </nav>

  <section class="hero wrap" role="img" aria-label="Photo of a speech therapist working with young children in a classroom">
    <p class="hero-caption">We are doing consultancy practice in the area of speech, language, and reading disabilities.</p>
    <div class="hero-dots"><i class="on"></i><i></i><i></i><i></i></div>
  </section>

  <section class="welcome wrap">
    <h2 class="section-title">Welcome to Our Website</h2>
    <p>Lorem ipsum dolor sit amet, consectetur adipiscing elit, sed diam nonummy nibh euismod tincidunt ut laoreet dolore magna aliquam erat volutpat. Ut wisi enim ad minim veniam, quis nostrud exerci tation ullamcorper suscipit lobortis nisl ut aliquip ex ea commodo consequat. Duis autem vel eum iriure dolor in hendrerit in vulputate velit esse molestie consequat.</p>
    <a class="read-more" href="#">READ MORE &gt;</a>
  </section>

  <section class="services">
    <div class="wrap">
      <h2 class="section-title">What We Do</h2>
      <div class="service-grid">
        <article class="service-card">
          <div class="service-media m1" role="img" aria-label="Photo of a child using a tablet for communication"></div>
          <h3>ASSISTIVE TECHNOLOGY</h3>
          <p>Lorem ipsum dolor sit amet, consectetur adipiscing elit, sed diam nonummy nibh euismod tincidunt ut laoreet dolore magna.</p>
          <a class="learn-more" href="#">Learn More &gt;</a>
        </article>
        <article class="service-card">
          <div class="service-media m2" role="img" aria-label="Photo of a parent and toddler learning together"></div>
          <h3>EARLY LANGUAGE LEARNING</h3>
          <p>Lorem ipsum dolor sit amet, consectetur adipiscing elit, sed diam nonummy nibh euismod tincidunt ut laoreet dolore magna.</p>
          <a class="learn-more" href="#">Learn More &gt;</a>
        </article>
        <article class="service-card">
          <div class="service-media m3" role="img" aria-label="Photo of a tutor helping a child with reading"></div>
          <h3>READING DIFFICULTIES</h3>
          <p>Lorem ipsum dolor sit amet, consectetur adipiscing elit, sed diam nonummy nibh euismod tincidunt ut laoreet dolore magna.</p>
          <a class="learn-more" href="#">Learn More &gt;</a>
        </article>
      </div>
    </div>
  </section>

  <section class="lower wrap">
    <div class="research">
      <h2>Research Updates 365</h2>
      <div class="research-body">
        <div class="research-media" role="img" aria-label="Photo of a printed page with the word research highlighted"></div>
        <ul class="updates">
          <li><svg width="9" height="8" viewBox="0 0 9 8"><path d="M1 4l2.5 2.5L8 1" fill="none" stroke="#2878bf" stroke-width="1.6"/></svg>Using assistive technology for communication for children with autism.</li>
          <li><svg width="9" height="8" viewBox="0 0 9 8"><path d="M1 4l2.5 2.5L8 1" fill="none" stroke="#2878bf" stroke-width="1.6"/></svg>Early intervention with focus on parent participation.</li>
          <li><svg width="9" height="8" viewBox="0 0 9 8"><path d="M1 4l2.5 2.5L8 1" fill="none" stroke="#2878bf" stroke-width="1.6"/></svg>Language learning for children birth-to-five years.</li>
        </ul>
      </div>
      <a class="read-more" href="#">READ MORE &gt;</a>
    </div>
    <div class="pro-dev">
      <h2>Professional development</h2>
      <div class="pd-item">
        <div class="pd-media" role="img" aria-label="Photo of a professional workshop"></div>
        <p>Lorem ipsum dolor sit amet, consectetur adipiscing elit, sed diam nonummy.<small>Admin</small></p>
      </div>
      <div class="pd-item">
        <div class="pd-media" role="img" aria-label="Photo of a training session"></div>
        <p>Lorem ipsum dolor sit amet, consectetur adipiscing elit, sed diam nonummy.<small>Admin</small></p>
      </div>
    </div>
  </section>

  <footer class="site-footer">
    <div class="wrap">
      <div class="footer-links"><a href="#">Home</a> &nbsp;|&nbsp; <a href="#">Consultation</a> &nbsp;|&nbsp; <a href="#">Research</a> &nbsp;|&nbsp; <a href="#">Professional Development</a> &nbsp;|&nbsp; <a href="#">Contact</a></div>
      <div class="copyright">Copyright © 2016 Larkhollow Consultants. All Rights Reserved</div>
      <div class="connect"><span>Connect Us</span><div class="social"><i></i><i></i><i></i></div></div>
    </div>
  </footer>
</body>
</html>
```